Create modern and sleek business card for luxury real estate company

We're a "boutique" real estate office looking for a design that gets across a highly modern luxury brand. Blacks and whites are probably the best colors unless we try a silver foil for the logo. I've attached a version of our current logo here. I'd like to swap out the current font on there with Gotham Light Regular.

I'm looking to have one side of the card have the logo with the space for our agents info on the other side.

Target Market(s)

Young professionals in a "luxury" headspace

Industry/Entity Type

Real estate

Contact Information for Business Card

A place for agent name, cell number, website. The slogan "Simply Rethinking Real Estate".

Font styles to use
Other font styles liked:
• Gotham Regular

Colors

Designer to choose only greyscale colors for use in the design.

Requirements
Must have
• Matte black as the background color. Clean lines and use of contrast. A specific design aspect that will use silver foil.
Nice to have
• Up in the air on integrating a QR code
Should not have
• Any houses or other real estate related design (ex: a clip art house)

```html
<!DOCTYPE html>
<html lang="en">
<head>
<meta charset="utf-8">
<title>Halden Estates – Business Card</title>
<link href="https://fonts.googleapis.com/css2?family=Lato:wght@400&family=Tinos:wght@400;700&display=swap" rel="stylesheet">
<style>
  :root {
    --page-bg: #a4a4a4;
    --card-dark: #333333;
    --card-light: #ffffff;
    --ink: #1c1c1c;
    --silver: #ececec;
    --rule: #9a9a9a;
  }
  html, body {
    margin: 0;
    width: 1200px;
    height: 1200px;
    overflow: hidden;
    background: var(--page-bg);
  }
  .stage { position: relative; width: 1200px; height: 1200px; }
  .card {
    position: absolute;
    top: 303px;
    width: 370px;
    height: 594px;
    overflow: hidden;
    box-shadow: 3px 4px 6px rgba(0,0,0,0.35);
  }
  .card--front { left: 200px; background: var(--card-dark); }
  .card--back { left: 599px; width: 365px; background: var(--card-light); color: var(--ink); }

  .brand {
    position: absolute;
    display: flex;
    align-items: center;
  }
  .brand__circle {
    border-radius: 50%;
    box-sizing: border-box;
    flex: none;
  }
  .brand__name {
    font-family: "Tinos", serif;
    font-weight: 400;
    line-height: 1.05;
    text-transform: uppercase;
  }
  .card--front .brand { left: 26px; top: 444px; gap: 22px; }
  .card--front .brand__circle { width: 90px; height: 90px; border: 3px solid var(--silver); }
  .card--front .brand__name { color: var(--silver); font-size: 40px; }

  .card--back .brand { left: 39px; top: 103px; gap: 22px; }
  .card--back .brand__circle { width: 80px; height: 80px; border: 3px solid var(--ink); }
  .card--back .brand__name { color: var(--ink); font-size: 38px; }

  .agent {
    position: absolute;
    left: 0; right: 0; top: 330px;
    text-align: center;
  }
  .agent__name {
    font-family: "Tinos", serif;
    font-weight: 700;
    font-size: 25px;
    letter-spacing: 1px;
    margin: 0;
    line-height: 1;
  }
  .agent__role {
    font-family: "Lato", sans-serif;
    font-size: 16px;
    margin: 3px 0 0;
  }
  .contact-icons {
    position: absolute;
    left: 88px; top: 395px;
    width: 190px;
    height: 26px;
    display: flex;
    align-items: center;
    justify-content: center;
    gap: 4px;
  }
  .contact-icons__rule { flex: 1; height: 1px; background: var(--rule); }
  .contact-icons__rule--left { margin-right: 4px; }
  .contact-icons__rule--right { margin-left: 4px; }
  .icon {
    width: 25px; height: 25px;
    background: var(--ink);
    border-radius: 4px;
    display: flex; align-items: center; justify-content: center;
  }
  .contact-lines, .address {
    position: absolute;
    left: 0; right: 0;
    text-align: center;
    font-family: "Lato", sans-serif;
    font-size: 16.5px;
    line-height: 22px;
    margin: 0;
  }
  .contact-lines { top: 430px; }
  .divider {
    position: absolute;
    left: 88px; top: 507px;
    width: 194px; height: 1px;
    background: var(--rule);
  }
  .address { top: 517px; }
</style>
</head>
<body>
<main class="stage">
  <section class="card card--front" aria-label="Card front">
    <div class="brand">
      <span class="brand__circle"></span>
      <span class="brand__name">Halden<br>Estates</span>
    </div>
  </section>

  <section class="card card--back" aria-label="Card back">
    <div class="brand">
      <span class="brand__circle"></span>
      <span class="brand__name">Halden<br>Estates</span>
    </div>

    <div class="agent">
      <h1 class="agent__name">MARCUS HALE</h1>
      <p class="agent__role">Managing Director</p>
    </div>

    <div class="contact-icons">
      <span class="contact-icons__rule contact-icons__rule--left"></span>
      <span class="icon" aria-label="Phone">
        <svg width="15" height="15" viewBox="0 0 16 16"><path d="M2 5c0-2 3-3 6-3s6 1 6 3v1h-3V5H5v1H2z M4 7h8l1 7H3z" fill="#fff"/></svg>
      </span>
      <span class="icon" aria-label="Email">
        <svg width="15" height="15" viewBox="0 0 16 16"><rect x="1.5" y="3.5" width="13" height="9" fill="none" stroke="#fff" stroke-width="1.3"/><path d="M1.5 3.5 8 9l6.5-5.5" fill="none" stroke="#fff" stroke-width="1.3"/></svg>
      </span>
      <span class="icon" aria-label="Website">
        <svg width="15" height="15" viewBox="0 0 16 16"><circle cx="8" cy="8" r="6.5" fill="none" stroke="#fff" stroke-width="1.3"/><ellipse cx="8" cy="8" rx="2.8" ry="6.5" fill="none" stroke="#fff" stroke-width="1.1"/><path d="M1.5 8h13" stroke="#fff" stroke-width="1.1"/></svg>
      </span>
      <span class="contact-icons__rule contact-icons__rule--right"></span>
    </div>

    <p class="contact-lines">044-555 010 234<br>info@haldenestates.com<br>www.haldenestates.com</p>
    <span class="divider"></span>
    <p class="address">87, Linden Row<br>60318, Northvale</p>
  </section>
</main>
</body>
</html>
```